I need a simple infographic that describes the 4 basic elements of how to effectively create change.

The overall title (Gentle Pressure Relentlessly Applied) should be at the top of the infographic. Subtitle is: "Leading Change".
There are four steps:
1. Alignment- Agreement on Approach
2. Transparency- Metrics for Assurance
3. Skills- Training and Coaching
4. Integrity- Culture of Accountability

Target Market(s)

Business Leaders in a training workshop

Font styles to use
Serif

Requirements
Must have
• Here are the 4 elements of the Infographic: Please show them in order.
• 1. Agreement on Approach. (Alignment)
• 2. Metrics for Assurance (Transparency)
• 3. Training and Coaching (Skills)
• 4. Culture of Accountability (Integrity)
Nice to have
• Cool Graphics that depict the 4 steps.
Should not have
• Pictures.

```html
<!DOCTYPE html>
<html lang="en">
<head>
<meta charset="utf-8">
<title>Leading Change – The Hale Group</title>
<link href="https://fonts.googleapis.com/css2?family=Roboto:wght@300;700&family=Source+Sans+3:wght@600;700&display=swap" rel="stylesheet">
<style>
  :root {
    --bg: #c1c9cc;
    --blue-light: #2bc3f1;
    --blue-mid: #08aeec;
    --blue-deep: #0093d8;
    --accent: #2aa6da;
    --ink: #111;
    --text-dark: #333;
    --panel-light: #ffffff;
    --panel-dark: #c3c5c8;
    --white: #ffffff;
  }
  * { margin: 0; padding: 0; box-sizing: border-box; }
  html, body { width: 1153px; height: 1200px; overflow: hidden; background: var(--bg); }
  .canvas { position: relative; width: 1153px; height: 1200px; }
  .card-shape { position: absolute; left: 0; top: 0; }

  .brand {
    position: absolute; left: 148px; top: 331px;
    display: flex; align-items: center; gap: 12px;
    color: var(--white);
    font-family: "Roboto", sans-serif; font-weight: 300;
    font-size: 35px; letter-spacing: 0.5px; line-height: 1;
  }
  .brand-dot { width: 58px; height: 58px; border: 3px solid var(--white); border-radius: 50%; }

  .headline { position: absolute; left: 148px; top: 418px; color: var(--white); font-family: "Roboto", sans-serif; }
  .headline-title { font-weight: 700; font-size: 30.5px; line-height: 1; }
  .headline-sub { font-weight: 300; font-size: 27px; letter-spacing: 3px; line-height: 1; margin-top: 1px; }

  .steps { position: absolute; left: 102px; top: 485px; display: flex; }
  .step {
    width: 237px; height: 337px; position: relative; text-align: center;
    background: linear-gradient(90deg, var(--panel-light) 30%, var(--panel-dark) 100%);
    font-family: "Source Sans 3", sans-serif;
  }
  .step-number { position: absolute; top: 18px; left: 0; right: 0; font-weight: 700; font-size: 56px; color: var(--accent); line-height: 1; }
  .step-icon { position: absolute; top: 112px; left: 50%; transform: translateX(-50%); width: 100px; height: 100px; }
  .step-icon-placeholder { border-radius: 8px; background: linear-gradient(135deg, #e6e8ea, #b9bcc0); }
  .step-rule { position: absolute; top: 260px; left: 25px; width: 177px; height: 2px; background: var(--accent); }
  .step-title { position: absolute; top: 268px; left: 0; right: 0; font-weight: 700; font-size: 24px; color: var(--accent); line-height: 1.1; }
  .step-desc { position: absolute; top: 297px; left: 0; right: 0; font-weight: 600; font-size: 15px; color: var(--text-dark); }
</style>
</head>
<body>
<div class="canvas">
  <svg class="card-shape" width="1153" height="1200" viewBox="0 0 1153 1200" aria-hidden="true">
    <defs>
      <linearGradient id="cardBlue" x1="0" x2="1" y1="0" y2="0">
        <stop offset="0" stop-color="var(--blue-light)"/>
        <stop offset="0.5" stop-color="var(--blue-mid)"/>
        <stop offset="1" stop-color="var(--blue-deep)"/>
      </linearGradient>
      <linearGradient id="bandBlue" x1="0" x2="1" y1="0" y2="0">
        <stop offset="0" stop-color="#2cc5f2"/>
        <stop offset="0.55" stop-color="#06b0ee"/>
        <stop offset="1" stop-color="#0096da"/>
      </linearGradient>
      <filter id="glow" x="-10%" y="-15%" width="120%" height="130%">
        <feGaussianBlur stdDeviation="9"/>
      </filter>
    </defs>
    <path d="M102,394 Q102,304 192,304 L560,304 C610,304 620,340 650,375 C675,402 690,406 730,406 L960,406 Q1050,406 1050,496 L1050,790 Q1050,890 950,890 L202,890 Q102,890 102,790 Z" fill="#4cc6ee" opacity="0.6" filter="url(#glow)"/>
    <path d="M102,394 Q102,304 192,304 L560,304 C610,304 620,340 650,375 C675,402 690,406 730,406 L960,406 Q1050,406 1050,496 L1050,790 Q1050,890 950,890 L202,890 Q102,890 102,790 Z" fill="url(#cardBlue)"/>
    <g class="bands">
      <path d="M102,822 L339,822 L339,890 L202,890 Q130,890 102,822 Z" fill="url(#bandBlue)"/>
      <rect x="339" y="822" width="237" height="68" fill="url(#bandBlue)"/>
      <rect x="576" y="822" width="237" height="68" fill="url(#bandBlue)"/>
      <path d="M813,822 L1050,822 Q1022,890 950,890 L813,890 Z" fill="url(#bandBlue)"/>
    </g>
  </svg>

  <div class="brand"><span class="brand-dot"></span><span>THE HALE GROUP</span></div>

  <div class="headline">
    <div class="headline-title">GENTLE PRESSURE RELENTLESSLY APPLIED</div>
    <div class="headline-sub">LEADING CHANGE</div>
  </div>

  <div class="steps">
    <section class="step">
      <div class="step-number">1</div>
      <div class="step-icon step-icon-placeholder" role="img" aria-label="Handshake icon"></div>
      <div class="step-rule"></div>
      <h2 class="step-title">Alignment</h2>
      <p class="step-desc">Agreement on Approach</p>
    </section>
    <section class="step">
      <div class="step-number">2</div>
      <svg class="step-icon" viewBox="0 0 100 100" aria-label="Magnifying glass icon" role="img">
        <circle cx="38" cy="36" r="30" fill="none" stroke="var(--ink)" stroke-width="4"/>
        <circle cx="38" cy="36" r="22" fill="none" stroke="var(--ink)" stroke-width="3"/>
        <circle cx="38" cy="36" r="7" fill="var(--ink)"/>
        <line x1="60" y1="58" x2="68" y2="66" stroke="var(--ink)" stroke-width="6"/>
        <rect x="66" y="62" width="12" height="34" rx="6" transform="rotate(-45 72 79)" fill="none" stroke="var(--ink)" stroke-width="4"/>
      </svg>
      <div class="step-rule"></div>
      <h2 class="step-title">Transparency</h2>
      <p class="step-desc">Metrics for Assurance</p>
    </section>
    <section class="step">
      <div class="step-number">3</div>
      <div class="step-icon step-icon-placeholder" role="img" aria-label="Presenter at a board icon"></div>
      <div class="step-rule"></div>
      <h2 class="step-title">Skills</h2>
      <p class="step-desc">Training and Coaching</p>
    </section>
    <section class="step">
      <div class="step-number">4</div>
      <svg class="step-icon" viewBox="0 0 100 100" aria-label="Scales of justice icon" role="img">
        <g fill="none" stroke="var(--ink)" stroke-width="3.5" stroke-linejoin="round">
          <circle cx="50" cy="8" r="4"/>
          <line x1="50" y1="12" x2="50" y2="88"/>
          <line x1="15" y1="24" x2="85" y2="24"/>
          <path d="M17,24 L4,60 M17,24 L30,60 M2,60 Q17,80 32,60 Z"/>
          <path d="M83,24 L70,60 M83,24 L96,60 M68,60 Q83,80 98,60 Z"/>
          <path d="M30,96 Q34,86 50,86 Q66,86 70,96 Z"/>
        </g>
      </svg>
      <div class="step-rule"></div>
      <h2 class="step-title">Integrity</h2>
      <p class="step-desc">Culture of Accountability</p>
    </section>
  </div>
</div>
</body>
</html>
```